BRIGHTHOLD PROPERTY MANAGEMENT INC. WEBSITE

Please make the website more family-friendly.

I want a website to help me build my property management business by adding listing properties and creating an online application. Im open to any other ideas.
I want a WordPress designer to code it.

Here is my current website. www.brighthold.biz

IDEA: I like the website design https://www.pelicanclimateservices.com/

Thank you

Tom

Number of Pages Required

5+ page

```html
<!DOCTYPE html>
<html lang="en">
<head>
<meta charset="utf-8">
<title>Brighthold Property Management – Homepage Concepts</title>
<link rel="stylesheet" href="https://fonts.googleapis.com/css2?family=Cinzel:wght@400;500;600&family=Poppins:wght@300;400;500;600&display=swap">
<style>
:root{
  --red:#a50f16;
  --red-dark:#8c0c12;
  --ink:#222;
  --muted:#666;
  --board:#dedede;
  --hero:#ececec;
  --band:#f3f3f3;
  --line:#d8d8d8;
  --footer:#111;
  --white:#fff;
}
*{box-sizing:border-box;margin:0;padding:0}
html,body{width:1021px;height:1200px;overflow:hidden;background:var(--board)}
body{font-family:"Poppins",sans-serif;color:var(--ink)}
.board{position:absolute;left:0;top:0;width:1764px;height:2074px;transform:scale(.5788);transform-origin:0 0;background:var(--board)}
.arrows{position:absolute;left:0;top:0}
.page{position:absolute;background:var(--white);overflow:hidden}
.page > *{position:absolute}
.page-a{left:440px;top:69px;width:350px;height:1935px}
.page-b{left:889px;top:70px;width:367px;height:1934px}

/* header */
.topbar{left:0;top:0;width:100%;height:14px;background:var(--red)}
.util{position:absolute;top:3px;display:flex;gap:10px;font-size:4px;color:var(--white)}
.search{position:absolute;top:3px;height:9px;background:#c9333a;border-radius:1px;font-size:3.6px;color:#f4d0d2;padding:2.5px 4px}
.logo{display:flex;align-items:center;gap:3px;font-family:"Cinzel",serif;font-weight:600;color:var(--red)}
.logo .mark{width:7px;height:7px;background:var(--red)}
.menu{display:flex;gap:7px;font-size:3.8px;color:#444}
.hero{left:0;width:100%}
.hero-title{font-family:"Cinzel",serif;font-weight:500;color:var(--red);letter-spacing:.5px;line-height:1}
.hero-sub{color:#333;line-height:1.45}
.hero-sub .hot{color:var(--red);font-weight:500}
.photo{border-radius:1px}

/* shared text */
.eyebrow{font-size:6px;color:var(--red);letter-spacing:.3px}
.heading{font-family:"Cinzel",serif;font-weight:500;color:var(--ink);letter-spacing:.6px;line-height:1}
.rule{height:1px;width:14px;background:var(--red)}
.center{text-align:center}
.para{font-size:3.6px;line-height:7.4px;color:#666}
.para .call{display:block;color:var(--red);font-size:5.2px;margin-top:2px}
.btn{display:flex;align-items:center;gap:3px}
.btn .mark{width:12px;height:17px;background:var(--red)}
.btn span{background:var(--red);color:var(--white);font-size:4.2px;font-weight:500;padding:5px 9px}

/* services wheel */
.ring{border-radius:50%;background:var(--white);box-shadow:0 0 6px rgba(0,0,0,.18);display:flex;align-items:center;justify-content:center}
.ring .core{border-radius:50%;background:radial-gradient(circle at 55% 45%,#cdbd6f 0,#8aa442 35%,#4f7a2c 70%,#3a5c22 100%)}
.ico{width:15px;height:15px;border-radius:50%;background:var(--red);box-shadow:0 0 0 1.5px var(--white),0 0 0 2.3px var(--red);display:flex;align-items:center;justify-content:center}
.ico::after{content:"";width:6px;height:6px;border:1.2px solid var(--white);border-radius:1.5px}
.svc{font-size:4.4px;font-weight:600;color:#333;line-height:1.2}

/* qualifying */
.band{left:0;width:100%;background:var(--band)}
.q-ico{width:16px;height:16px;border-radius:50%;border:1.3px solid var(--red);background:var(--white);display:flex;align-items:center;justify-content:center}
.q-ico::after{content:"";width:6px;height:6px;border-radius:50%;background:var(--red)}
.q-label{font-size:3.6px;color:#444;text-align:center;width:40px;line-height:1.3}
.qual-box{background:var(--red);border-radius:3px}
.qual-box .q-ico{border-color:var(--white);box-shadow:0 0 0 1px var(--white)}
.qual-box .q-label{color:var(--white)}

/* listings */
.tab{display:flex;align-items:center;justify-content:center;font-size:6px;letter-spacing:.3px}
.tab-on{background:var(--red);color:var(--white)}
.tab-off{background:#e6e6e6;color:#555}
.filter{display:flex;align-items:center;gap:4px;padding:3px 4px;background:var(--white);box-shadow:0 0 4px rgba(0,0,0,.2)}
.filter .f{height:15px;border:1px solid #cfcfcf;font-size:3.4px;color:#555;padding:5px 3px}
.filter .go{height:15px;background:var(--red);color:var(--white);font-size:3.4px;padding:5px 5px}
.card{border:1px solid #cfcfcf;background:var(--white)}
.card-photo{width:100%}
.card-body{padding:6px 6px;font-size:3.3px;color:#444;line-height:1.45}
.card-title{color:var(--red);font-weight:600;margin-top:4px}
.card-addr{margin:3px 0}
.card-meta{display:flex;justify-content:space-between}
.card-meta b{font-weight:500;color:var(--red)}
.mini-btn{display:inline-block;margin-top:4px;background:var(--red);color:var(--white);font-size:3px;padding:2px 5px}
.pager{font-size:9px;color:#333;letter-spacing:2px}

/* contact */
.contact-photo{background:linear-gradient(160deg,#b8b8b8 0,#8f8f8f 55%,#7a5a3a 100%)}
.field{border:1px solid #eee;background:#fcfcfc;box-shadow:0 0 2px rgba(0,0,0,.06);font-size:3.5px;color:#888;padding:4px 6px}
.submit{background:var(--red);color:var(--white);font-size:4px;font-weight:500;display:flex;align-items:center;justify-content:center}

/* testimonials */
.quotes-bg{background:var(--red)}
.quotes-title{font-family:"Cinzel",serif;font-weight:500;color:var(--white);font-size:12px;letter-spacing:.4px}
.quotes-sub{font-family:"Cinzel",serif;color:var(--white);font-size:4.6px;letter-spacing:.4px}
.quotes-tag{color:var(--white);font-size:4.6px}
.quote{background:#ececec;border-radius:2px;padding:8px 8px;font-size:3.4px;line-height:6.2px;color:#555}
.quote .who{display:flex;align-items:center;gap:5px;margin-bottom:7px;font-size:4px;color:var(--red)}
.quote .avatar{width:14px;height:14px;border-radius:50%;background:linear-gradient(#c9c3bd,#8e857d)}
.quote .mark-q{margin-left:auto;font-family:"Cinzel",serif;font-size:10px;color:#cfcfcf}
.nav-dot{width:7px;height:7px;border-radius:50%;background:var(--red)}

/* footer */
.footer{left:0;width:100%;background:var(--footer)}
.foot-col{color:#ddd;font-size:3.5px;line-height:6.3px}
.foot-col h4{font-family:"Cinzel",serif;font-weight:400;font-size:4.2px;color:var(--white);letter-spacing:.4px;margin-bottom:7px}
.foot-col li{list-style:none;padding-left:5px;position:relative}
.foot-col li::before{content:"";position:absolute;left:0;top:2.5px;width:1.6px;height:1.6px;background:#ddd;border-radius:50%}
.foot-row{display:flex;gap:4px;margin-bottom:3px}
.foot-row i{flex:none;width:6px;height:6px;border:.8px solid #ddd;border-radius:1px}
.foot-input{height:8px;background:var(--white);margin:3px 0 6px}
.foot-btn{display:inline-block;background:var(--red);color:var(--white);font-size:3px;padding:2px 5px}
.socials{display:flex;gap:3px}
.socials i{width:6px;height:6px;border-radius:50%;background:var(--red)}
.legal{left:0;width:100%;background:var(--red)}
.legal p{position:absolute;font-size:3px;color:#f3d4d5;line-height:4.6px}
.badges{position:absolute;display:flex;gap:6px;align-items:center}
.badges i{display:block;border:1.4px solid var(--white)}
</style>
</head>
<body>
<div class="board">

<svg class="arrows" width="1764" height="2074" viewBox="0 0 1764 2074" aria-hidden="true">
  <g fill="none" stroke="#8a8a8a" stroke-width="6" stroke-linecap="round" stroke-linejoin="round">
    <path d="M274 270 C310 258 345 250 376 246 M356 232 L378 246 L362 262"/>
    <path d="M285 1105 C315 1098 345 1096 368 1100 M358 1086 L370 1100 L360 1115"/>
    <path d="M1362 186 C1345 188 1326 190 1308 195 M1320 181 L1306 195 L1322 205"/>
    <path d="M1416 1024 C1395 1024 1366 1027 1342 1031 M1358 1016 L1340 1031 L1360 1046"/>
  </g>
</svg>

<!-- ================= CONCEPT A ================= -->
<main class="page page-a">
  <header class="topbar">
    <div class="util" style="left:148px">⌂ Home<span>✉ Contact</span><span>◯ Login</span></div>
    <div class="search" style="left:250px;width:77px">Search</div>
  </header>
  <div class="logo" style="left:24px;top:24px;font-size:9px"><i class="mark"></i>BRIGHTHOLD</div>
  <nav class="menu" style="left:146px;top:27px"><span>Listings▾</span><span>Owners▾</span><span>Prospect Tenants▾</span><span>About▾</span><span>Community▾</span><span>Mortgage Info▾</span></nav>

  <section class="hero" style="top:48px;height:219px;background:var(--hero)"></section>
  <h1 class="hero-title" style="left:28px;top:96px;font-size:26px">Call Today</h1>
  <p class="hero-sub" style="left:30px;top:127px;font-size:12.2px">And Get 1 Month<br>Property Management<br>Fee Off.$120 Value!!</p>
  <div class="btn" style="left:30px;top:193px"><i class="mark"></i><span>CONTACT US</span></div>
  <div class="photo" role="img" aria-label="Smiling family of four sitting together on the floor" style="left:120px;top:110px;width:215px;height:135px;background:radial-gradient(ellipse at 55% 55%,#6d7d99 0,#a9a39b 45%,rgba(236,236,236,0) 72%)"></div>

  <div role="img" aria-label="Model house in a hand" style="left:22px;top:293px;width:96px;height:103px;background:linear-gradient(160deg,#1d2a44 0,#3c4a66 45%,#e6e2da 46%,#c7372f 75%,#ede9e2 100%)"></div>
  <div role="img" aria-label="Two-storey suburban house" style="left:69px;top:338px;width:94px;height:103px;background:linear-gradient(#4f88c9 0,#88b3de 35%,#a89a84 60%,#6f8a4c 100%)"></div>
  <svg style="left:12px;top:318px" width="160" height="120" aria-hidden="true"><path d="M8 60 V110 H40 M120 0 H134 V12" fill="none" stroke="#a50f16" stroke-width=".8"/></svg>
  <p class="eyebrow" style="left:188px;top:298px">ABOUT US</p>
  <h2 class="heading" style="left:188px;top:310px;font-size:16px">Brighthold</h2>
  <i class="rule" style="left:188px;top:331px"></i>
  <p class="para" style="left:189px;top:339px;width:140px">Our goal at Brighthold is to give families the most caring rental service in the region. We focus on a more personal service for you and your tenants. We are a one-stop shop, no middle man, so no time is wasted.</p>
  <p class="para" style="left:189px;top:384px;width:140px">Brighthold is owned and run by Daniel Moreno, with over ten years of experience.</p>
  <div class="btn" style="left:190px;top:409px"><i class="mark"></i><span>KNOW MORE</span></div>

  <p class="eyebrow center" style="left:0;width:100%;top:486px">BRIGHTHOLD</p>
  <h2 class="heading center" style="left:0;width:100%;top:498px;font-size:13.5px">Property Management Services</h2>
  <i class="rule" style="left:168px;top:517px"></i>
  <div class="ring" style="left:112px;top:548px;width:130px;height:130px"><div class="core" role="img" aria-label="House model with a for-rent sign on green lawn" style="width:104px;height:104px"></div></div>
  <i class="ico" style="left:112px;top:542px"></i><p class="svc" style="left:70px;top:543px;text-align:right">Accounting<br>Services</p>
  <i class="ico" style="left:222px;top:541px"></i><p class="svc" style="left:246px;top:542px">Leasing</p>
  <i class="ico" style="left:86px;top:595px"></i><p class="svc" style="left:34px;top:596px;text-align:right">Mortgage<br>Utility Payments</p>
  <i class="ico" style="left:251px;top:595px"></i><p class="svc" style="left:273px;top:596px">Security<br>Deposits</p>
  <i class="ico" style="left:104px;top:656px"></i><p class="svc" style="left:66px;top:660px;text-align:right">Rent<br>Colections</p>
  <i class="ico" style="left:235px;top:652px"></i><p class="svc" style="left:259px;top:654px">Inspections of<br>Property</p>
  <i class="ico" style="left:170px;top:687px"></i><p class="svc center" style="left:140px;top:708px;width:75px">Repair &amp; Maintenance<br>Services</p>

  <p class="eyebrow" style="left:22px;top:782px">BRIGHTHOLD</p>
  <h2 class="heading" style="left:22px;top:793px;font-size:15px">Prospect Tenants</h2>
  <i class="rule" style="left:22px;top:812px"></i>
  <p class="para" style="left:22px;top:824px;width:140px">We know you have a choice in places to live and we truly thank you for choosing one of our homes. We want you to enjoy an easy stay, so if you have any questions or need any help, call us.<span class="call">Please call immediately at 555-014-2263.</span></p>
  <div class="btn" style="left:22px;top:879px"><i class="mark"></i><span>KNOW MORE</span></div>
  <div role="img" aria-label="Family carrying moving boxes into a bright new home" style="left:193px;top:778px;width:134px;height:131px;background:linear-gradient(160deg,#f4f1ec 0,#e0d8cc 50%,#b8946a 100%)"></div>

  <section class="band" style="top:961px;height:130px"></section>
  <p class="eyebrow center" style="left:0;width:100%;top:987px;font-size:5px">RENTAL APPLICANTS AND PROSPECTIVE TENANTS</p>
  <h2 class="heading center" style="left:0;width:100%;top:998px;font-size:13.5px">Qualifying for a Rental</h2>
  <i class="rule" style="left:168px;top:1016px"></i>
  <i class="q-ico" style="left:56px;top:1035px"></i><p class="q-label" style="left:44px;top:1057px">INCOME</p>
  <i class="q-ico" style="left:99px;top:1035px"></i><p class="q-label" style="left:87px;top:1057px">CREDIT REPORTS</p>
  <i class="q-ico" style="left:144px;top:1035px"></i><p class="q-label" style="left:132px;top:1057px">REFERENCES</p>
  <i class="q-ico" style="left:188px;top:1035px"></i><p class="q-label" style="left:176px;top:1057px">PETS</p>
  <i class="q-ico" style="left:233px;top:1035px"></i><p class="q-label" style="left:221px;top:1057px">SELECTION<br>PROCESS</p>
  <i class="q-ico" style="left:276px;top:1035px"></i><p class="q-label" style="left:264px;top:1057px">SIGNING<br>A LEASE</p>

  <p class="eyebrow" style="left:22px;top:1127px">BRIGHTHOLD</p>
  <h2 class="heading" style="left:22px;top:1138px;font-size:15px">Listings</h2>
  <div class="tab tab-on" style="left:22px;top:1168px;width:100px;height:22px">ALL LISTINGS</div>
  <div class="tab tab-off" style="left:130px;top:1168px;width:101px;height:22px">FEATURED LISTINGS</div>
  <div class="filter" style="left:22px;top:1208px;width:305px;height:23px">
    <span class="f" style="width:93px">Enter Address</span><span class="f" style="width:36px">Min Price ▾</span><span class="f" style="width:36px">Max Price ▾</span><span class="f" style="width:40px">Structured Size ▾</span><span class="f" style="width:40px">Lot Size ▾</span><span class="go">SEARCH</span>
  </div>
  <article class="card" style="left:22px;top:1257px;width:97px;height:149px">
    <div class="card-photo" role="img" aria-label="Single-storey unit under a large tree" style="height:74px;background:linear-gradient(#5d88c3 0,#9fb6cf 45%,#b9a88c 70%,#7c6a52 100%)"></div>
    <div class="card-body"><p class="card-title">Fantastic opportunity<br>2 Bdrm x 1 Bth ADU Unit!</p><p class="card-addr">● Elm Street, Riverton, CA, US</p><div class="card-meta"><span><b>Status:</b> Available</span><span><b>Type:</b> Residential</span></div><div class="card-meta"><span><b>Size:</b> 693 Sq. Ft.</span><span>▪ 2 &nbsp;▪ 1</span></div><span class="mini-btn">CONTACT US</span></div>
  </article>
  <article class="card" style="left:126px;top:1257px;width:96px;height:149px">
    <div class="card-photo" role="img" aria-label="Aerial view of a tree-lined neighbourhood" style="height:74px;background:linear-gradient(#7fa6d6 0,#a9c2de 35%,#7b8c5a 60%,#4d6a36 100%)"></div>
    <div class="card-body"><p class="card-title">Fantastic opportunity<br>2 Bdrm x 1 Bth ADU Unit!</p><p class="card-addr">● Elm Street, Riverton, CA, US</p><div class="card-meta"><span><b>Status:</b> Available</span><span><b>Type:</b> Residential</span></div><div class="card-meta"><span><b>Size:</b> 693 Sq. Ft.</span><span>▪ 2 &nbsp;▪ 1</span></div><span class="mini-btn">CONTACT US</span></div>
  </article>
  <article class="card" style="left:230px;top:1257px;width:97px;height:149px">
    <div class="card-photo" role="img" aria-label="Modern house lit at dusk" style="height:74px;background:linear-gradient(#9487a9 0,#b9a4b8 35%,#5a5049 60%,#c9a26a 100%)"></div>
    <div class="card-body"><p class="card-title">Nice &amp; Clean 3 bd. x 1 bth.<br>Apartment.</p><p class="card-addr">● Elm Street, Riverton, CA, US</p><div class="card-meta"><span><b>Status:</b> Available</span><span><b>Type:</b> Residential</span></div><div class="card-meta"><span><b>Size:</b> 693 Sq. Ft.</span><span>▪ 3 &nbsp;▪ 1</span></div><span class="mini-btn">CONTACT US</span></div>
  </article>
  <p class="pager" style="left:163px;top:1415px"><span style="color:#bbb">←</span>→</p>

  <div class="contact-photo" role="img" aria-label="Red toy house beside a set of keys" style="left:36px;top:1478px;width:135px;height:160px"></div>
  <p class="eyebrow" style="left:201px;top:1477px">BRIGHTHOLD</p>
  <h2 class="heading" style="left:201px;top:1488px;font-size:15px">Contact Us</h2>
  <i class="rule" style="left:201px;top:1508px"></i>
  <div class="field" style="left:201px;top:1526px;width:111px;height:13px">Your Name</div>
  <div class="field" style="left:201px;top:1544px;width:111px;height:13px">Phone Number</div>
  <div class="field" style="left:201px;top:1562px;width:111px;height:13px">Email Address</div>
  <div class="field" style="left:201px;top:1580px;width:111px;height:27px">Message</div>
  <div class="submit" style="left:201px;top:1621px;width:48px;height:17px">SUBMIT</div>

  <section class="quotes-bg" style="left:0;top:1670px;width:168px;height:121px"></section>
  <h2 class="quotes-title" style="left:22px;top:1711px">BRIGHTHOLD</h2>
  <p class="quotes-sub" style="left:22px;top:1726px">PROPERTY MANAGEMENT</p>
  <p class="quotes-tag" style="left:22px;top:1744px">HAPPY CLIENTS</p>
  <i class="nav-dot" style="left:297px;top:1680px"></i><i class="nav-dot" style="left:311px;top:1680px"></i>
  <blockquote class="quote" style="left:108px;top:1696px;width:107px;height:73px"><div class="who"><i class="avatar" role="img" aria-label="Client portrait"></i>Mara Ellison<span class="mark-q">”</span></div>Moving in was easy and the team answered every call fast. Our family felt at home from day one, and repairs were done quickly.</blockquote>
  <blockquote class="quote" style="left:219px;top:1696px;width:107px;height:73px"><div class="who"><i class="avatar" role="img" aria-label="Client portrait"></i>Mara Ellison<span class="mark-q">”</span></div>Moving in was easy and the team answered every call fast. Our family felt at home from day one, and repairs were done quickly.</blockquote>

  <footer class="footer" style="top:1791px;height:105px"></footer>
  <div class="logo" style="left:24px;top:1845px;font-size:8px"><i class="mark"></i>BRIGHTHOLD</div>
  <div class="socials" style="left:29px;top:1871px"><i></i><i></i><i></i><i></i><i></i><i></i></div>
  <div class="foot-col" style="left:116px;top:1817px"><h4>QUICK LINKS</h4><ul><li>Listings</li><li>Owners</li><li>Prospect Tenants</li><li>About</li><li>Community</li><li>Mortgage Info</li></ul></div>
  <div class="foot-col" style="left:180px;top:1817px;width:75px"><h4>CONTACT US</h4><div class="foot-row"><i></i><span>(555) 014-5050<br>(555) 014-5263</span></div><div class="foot-row"><i></i><span>EMAIL US<br>hello@brighthold.biz</span></div><div class="foot-row"><i></i><span>480 Harbor Lane,<br>Riverton, CA 95800</span></div></div>
  <div class="foot-col" style="left:261px;top:1817px;width:66px"><h4>NEWSLETTER SIGN UP</h4><p>Subscribe to our newsletter to get the latest news.</p><div class="foot-input"></div><span class="foot-btn">SUBSCRIBE</span></div>
  <div class="legal" style="top:1896px;height:39px">
    <p style="left:22px;top:10px">An Equal Opportunity Company. Equal Housing Opportunity. All rights reserved.<br>Copyright 2024 BRIGHTHOLD PROPERTY MANAGEMENT INC. | Site by Northway Web Studio</p>
    <div class="badges" style="left:225px;top:12px"><i style="width:9px;height:11px"></i><i style="width:32px;height:11px"></i><i style="width:11px;height:11px"></i><i style="width:10px;height:11px"></i></div>
  </div>
</main>

<!-- ================= CONCEPT B ================= -->
<main class="page page-b">
  <header class="topbar" style="height:15px">
    <div class="util" style="left:156px">⌂ Home<span>✉ Contact</span><span>◯ Login</span></div>
    <div class="search" style="left:264px;width:80px">Search</div>
  </header>
  <div class="logo" style="left:25px;top:25px;font-size:9.4px"><i class="mark"></i>BRIGHTHOLD</div>
  <nav class="menu" style="left:154px;top:28px"><span>Listings▾</span><span>Owners▾</span><span>Prospect Tenants▾</span><span>About▾</span><span>Community▾</span><span>Mortgage Info▾</span></nav>

  <section class="hero" style="top:48px;height:142px;background:linear-gradient(90deg,#f3f3f3 0,#fafafa 60%,#e9e9e9 100%)"></section>
  <div class="photo" role="img" aria-label="Happy family of three under a white sheet fort" style="left:175px;top:48px;width:192px;height:142px;background:radial-gradient(ellipse at 55% 55%,#d8cfc7 0,#ece8e4 45%,rgba(244,244,244,0) 80%)"></div>
  <h1 class="hero-title" style="left:23px;top:80px;font-size:28px">Call Today</h1>
  <p class="hero-sub" style="left:24px;top:110px;font-size:12.4px;line-height:1.6">And Get 1 Month<br>Property Management<br><span class="hot">Fee Off. $120 Value!!</span></p>

  <div role="img" aria-label="Model house in a hand" style="left:24px;top:211px;width:101px;height:108px;background:linear-gradient(160deg,#1d2a44 0,#3c4a66 45%,#e6e2da 46%,#c7372f 75%,#ede9e2 100%)"></div>
  <div role="img" aria-label="Two-storey suburban house" style="left:72px;top:259px;width:99px;height:108px;background:linear-gradient(#4f88c9 0,#88b3de 35%,#a89a84 60%,#6f8a4c 100%)"></div>
  <svg style="left:14px;top:235px" width="170" height="125" aria-hidden="true"><path d="M8 63 V108 H40 M125 0 H140 V12" fill="none" stroke="#a50f16" stroke-width=".8"/></svg>
  <p class="eyebrow" style="left:198px;top:217px">ABOUT US</p>
  <h2 class="heading" style="left:198px;top:229px;font-size:17px">Brighthold</h2>
  <i class="rule" style="left:198px;top:251px"></i>
  <p class="para" style="left:199px;top:259px;width:150px">Our goal at Brighthold is to give families the most caring rental service in the region. We focus on a more personal service for you and your tenants. We are a one-stop shop, no middle man, so no time is wasted.</p>
  <p class="para" style="left:199px;top:304px;width:150px">Brighthold is owned and run by Daniel Moreno, with over ten years of experience.</p>
  <div class="btn" style="left:199px;top:332px"><i class="mark"></i><span>KNOW MORE</span></div>

  <p class="eyebrow center" style="left:0;width:100%;top:413px">BRIGHTHOLD</p>
  <h2 class="heading center" style="left:0;width:100%;top:426px;font-size:15px">Property Management Services</h2>
  <i class="rule" style="left:177px;top:446px"></i>
  <div class="ring" style="left:116px;top:465px;width:140px;height:140px"><div class="core" role="img" aria-label="House model with a for-rent sign on green lawn" style="width:114px;height:114px"></div></div>
  <i class="ico" style="left:119px;top:473px"></i><p class="svc" style="left:78px;top:474px;text-align:right">Accounting<br>Services</p>
  <i class="ico" style="left:234px;top:471px"></i><p class="svc" style="left:257px;top:472px">Leasing</p>
  <i class="ico" style="left:92px;top:527px"></i><p class="svc" style="left:36px;top:528px;text-align:right">Mortgage<br>Utility Payments</p>
  <i class="ico" style="left:264px;top:527px"></i><p class="svc" style="left:287px;top:528px">Security<br>Deposits</p>
  <i class="ico" style="left:110px;top:593px"></i><p class="svc" style="left:72px;top:596px;text-align:right">Rent<br>Colections</p>
  <i class="ico" style="left:247px;top:588px"></i><p class="svc" style="left:271px;top:590px">Inspections of<br>Property</p>
  <i class="ico" style="left:179px;top:625px"></i><p class="svc center" style="left:149px;top:647px;width:75px">Repair &amp; Maintenance<br>Services</p>

  <p class="eyebrow" style="left:23px;top:722px">BRIGHTHOLD</p>
  <h2 class="heading" style="left:23px;top:734px;font-size:16px">Prospect Tenants</h2>
  <i class="rule" style="left:23px;top:754px"></i>
  <p class="para" style="left:23px;top:766px;width:150px">We know you have a choice in places to live and we truly thank you for choosing one of our homes. We want you to enjoy an easy stay, so if you have any questions or need any help, call us.<span class="call">Please call immediately at 555-014-2263.</span></p>
  <div class="btn" style="left:23px;top:823px"><i class="mark"></i><span>KNOW MORE</span></div>
  <div role="img" aria-label="Family carrying moving boxes into a bright new home" style="left:203px;top:719px;width:141px;height:140px;background:linear-gradient(160deg,#f4f1ec 0,#e0d8cc 50%,#b8946a 100%)"></div>

  <section class="qual-box" style="left:24px;top:911px;width:320px;height:128px"></section>
  <p class="eyebrow center" style="left:0;width:100%;top:929px;font-size:5px;color:#f6d6d8">RENTAL APPLICANTS AND PROSPECTIVE TENANTS</p>
  <h2 class="heading center" style="left:0;width:100%;top:940px;font-size:14.5px;color:#fff">Qualifying for a Rental</h2>
  <i class="rule" style="left:177px;top:960px;background:#fff"></i>
  <div class="qual-box" style="left:24px;top:980px;width:320px;height:40px;background:none">
    <i class="q-ico" style="position:absolute;left:41px;top:8px"></i><p class="q-label" style="position:absolute;left:29px;top:28px">INCOME</p>
    <i class="q-ico" style="position:absolute;left:82px;top:8px"></i><p class="q-label" style="position:absolute;left:70px;top:28px">CREDIT REPORTS</p>
    <i class="q-ico" style="position:absolute;left:125px;top:8px"></i><p class="q-label" style="position:absolute;left:113px;top:28px">REFERENCES</p>
    <i class="q-ico" style="position:absolute;left:169px;top:8px"></i><p class="q-label" style="position:absolute;left:157px;top:28px">PETS</p>
    <i class="q-ico" style="position:absolute;left:214px;top:8px"></i><p class="q-label" style="position:absolute;left:202px;top:28px">SELECTION<br>PROCESS</p>
    <i class="q-ico" style="position:absolute;left:254px;top:8px"></i><p class="q-label" style="position:absolute;left:242px;top:28px">SIGNING<br>A LEASE</p>
  </div>

  <p class="eyebrow" style="left:23px;top:1086px">BRIGHTHOLD</p>
  <h2 class="heading" style="left:23px;top:1098px;font-size:17px">Listings</h2>
  <div class="tab tab-on" style="left:24px;top:1129px;width:104px;height:24px">ALL LISTINGS</div>
  <div class="tab tab-off" style="left:137px;top:1129px;width:105px;height:24px">FEATURED LISTINGS</div>
  <div class="filter" style="left:24px;top:1172px;width:320px;height:23px">
    <span class="f" style="width:97px">Enter Address</span><span class="f" style="width:38px">Min Price ▾</span><span class="f" style="width:38px">Max Price ▾</span><span class="f" style="width:43px">Structured Size ▾</span><span class="f" style="width:43px">Lot Size ▾</span><span class="go">SEARCH</span>
  </div>
  <article class="card" style="left:24px;top:1222px;width:102px;height:157px">
    <div class="card-photo" role="img" aria-label="Single-storey unit under a large tree" style="height:79px;background:linear-gradient(#5d88c3 0,#9fb6cf 45%,#b9a88c 70%,#7c6a52 100%)"></div>
    <div class="card-body"><p class="card-title">Fantastic opportunity<br>2 Bdrm x 1 Bth ADU Unit!</p><p class="card-addr">● Elm Street, Riverton, CA, US</p><div class="card-meta"><span><b>Status:</b> Available</span><span><b>Type:</b> Residential</span></div><div class="card-meta"><span><b>Size:</b> 693 Sq. Ft.</span><span>▪ 2 &nbsp;▪ 1</span></div><span class="mini-btn">CONTACT US</span></div>
  </article>
  <article class="card" style="left:133px;top:1222px;width:102px;height:157px">
    <div class="card-photo" role="img" aria-label="Aerial view of a tree-lined neighbourhood" style="height:79px;background:linear-gradient(#7fa6d6 0,#a9c2de 35%,#7b8c5a 60%,#4d6a36 100%)"></div>
    <div class="card-body"><p class="card-title">Fantastic opportunity<br>2 Bdrm x 1 Bth ADU Unit!</p><p class="card-addr">● Elm Street, Riverton, CA, US</p><div class="card-meta"><span><b>Status:</b> Available</span><span><b>Type:</b> Residential</span></div><div class="card-meta"><span><b>Size:</b> 693 Sq. Ft.</span><span>▪ 2 &nbsp;▪ 1</span></div><span class="mini-btn">CONTACT US</span></div>
  </article>
  <article class="card" style="left:242px;top:1222px;width:102px;height:157px">
    <div class="card-photo" role="img" aria-label="Modern house lit at dusk" style="height:79px;background:linear-gradient(#9487a9 0,#b9a4b8 35%,#5a5049 60%,#c9a26a 100%)"></div>
    <div class="card-body"><p class="card-title">Nice &amp; Clean 3 bd. x 1 bth.<br>Apartment.</p><p class="card-addr">● Elm Street, Riverton, CA, US</p><div class="card-meta"><span><b>Status:</b> Available</span><span><b>Type:</b> Residential</span></div><div class="card-meta"><span><b>Size:</b> 693 Sq. Ft.</span><span>▪ 3 &nbsp;▪ 1</span></div><span class="mini-btn">CONTACT US</span></div>
  </article>
  <p class="pager" style="left:171px;top:1389px"><span style="color:#bbb">←</span>→</p>

  <div class="contact-photo" role="img" aria-label="Red toy house beside a set of keys" style="left:38px;top:1454px;width:143px;height:169px"></div>
  <p class="eyebrow" style="left:211px;top:1454px">BRIGHTHOLD</p>
  <h2 class="heading" style="left:211px;top:1465px;font-size:16px">Contact Us</h2>
  <i class="rule" style="left:211px;top:1486px"></i>
  <div class="field" style="left:211px;top:1505px;width:117px;height:14px">Your Name</div>
  <div class="field" style="left:211px;top:1524px;width:117px;height:14px">Phone Number</div>
  <div class="field" style="left:211px;top:1543px;width:117px;height:14px">Email Address</div>
  <div class="field" style="left:211px;top:1562px;width:117px;height:28px">Message</div>
  <div class="submit" style="left:211px;top:1604px;width:51px;height:18px">SUBMIT</div>

  <section class="quotes-bg" style="left:0;top:1655px;width:177px;height:127px"></section>
  <h2 class="quotes-title" style="left:23px;top:1699px;font-size:12.5px">BRIGHTHOLD</h2>
  <p class="quotes-sub" style="left:23px;top:1714px">PROPERTY MANAGEMENT</p>
  <p class="quotes-tag" style="left:23px;top:1733px">HAPPY CLIENTS</p>
  <i class="nav-dot" style="left:313px;top:1667px"></i><i class="nav-dot" style="left:328px;top:1667px"></i>
  <blockquote class="quote" style="left:114px;top:1682px;width:110px;height:78px"><div class="who"><i class="avatar" role="img" aria-label="Client portrait"></i>Mara Ellison<span class="mark-q">”</span></div>Moving in was easy and the team answered every call fast. Our family felt at home from day one, and repairs were done quickly.</blockquote>
  <blockquote class="quote" style="left:231px;top:1682px;width:112px;height:78px"><div class="who"><i class="avatar" role="img" aria-label="Client portrait"></i>Mara Ellison<span class="mark-q">”</span></div>Moving in was easy and the team answered every call fast. Our family felt at home from day one, and repairs were done quickly.</blockquote>

  <footer class="footer" style="top:1782px;height:110px"></footer>
  <div class="logo" style="left:25px;top:1838px;font-size:8.4px"><i class="mark"></i>BRIGHTHOLD</div>
  <div class="socials" style="left:31px;top:1865px"><i></i><i></i><i></i><i></i><i></i><i></i></div>
  <div class="foot-col" style="left:122px;top:1809px"><h4>QUICK LINKS</h4><ul><li>Listings</li><li>Owners</li><li>Prospect Tenants</li><li>About</li><li>Community</li><li>Mortgage Info</li></ul></div>
  <div class="foot-col" style="left:190px;top:1809px;width:78px"><h4>CONTACT US</h4><div class="foot-row"><i></i><span>(555) 014-5050<br>(555) 014-5263</span></div><div class="foot-row"><i></i><span>EMAIL US<br>hello@brighthold.biz</span></div><div class="foot-row"><i></i><span>480 Harbor Lane,<br>Riverton, CA 95800</span></div></div>
  <div class="foot-col" style="left:275px;top:1809px;width:69px"><h4>NEWSLETTER SIGN UP</h4><p>Subscribe to our newsletter to get the latest news.</p><div class="foot-input"></div><span class="foot-btn">SUBSCRIBE</span></div>
  <div class="legal" style="top:1892px;height:42px">
    <p style="left:23px;top:10px">An Equal Opportunity Company. Equal Housing Opportunity. All rights reserved.<br>Copyright 2024 BRIGHTHOLD PROPERTY MANAGEMENT INC. | Site by Northway Web Studio</p>
    <div class="badges" style="left:235px;top:13px"><i style="width:10px;height:12px"></i><i style="width:34px;height:12px"></i><i style="width:12px;height:12px"></i><i style="width:11px;height:12px"></i></div>
  </div>
</main>

</div>
</body>
</html>
```